Create a proposal + product powerpoint

Please see the powerpoint for the slides. There are about 20 slides to be created. Rest of them are for reference and show the design that I like.

I would like to move fast on this, since I need to present it next week (in the week of April 21st).

Please download the current content from here:
https://www.parcelbrook.net/fetch/qRtVmXzLwPkNbYcD

Please make at least 4 slides with the specific content so I can assess your design style.

Target Market(s)

Business Audience and very senior technical audience
Decision Makers

Industry/Entity Type

Product

Colors
e34297
a64599

Requirements
Must have
• Should be very clean, crisp.

I like to use Icons as shown in the powerpoint.... Please see the appendix of the slide deck that shows the various icons. Most of them just have plain text, and I would like to organize so that it does not look like some is just reading text.

I would like to focus on the design aspects so that the audience is clear on how the solution works.

Every page should some graphic element based on the slides shown in the appendix.

```html
<!DOCTYPE html>
<html lang="en">
<head>
<meta charset="utf-8">
<title>Key features</title>
<link rel="stylesheet" href="https://fonts.googleapis.com/css2?family=Roboto+Condensed:wght@400;500&display=swap">
<style>
  :root {
    --magenta: #a21ea0;
    --tile: #c24fb5;
    --tile-edge: #ffffff;
    --ink: #111111;
    --rule: #d6d6d6;
    --footer-dark: #9b1f5f;
    --footer-light: #a8479f;
    --white: #ffffff;
    --placeholder: #9a9a9a;
  }
  * { box-sizing: border-box; margin: 0; padding: 0; }
  html, body { width: 1200px; height: 900px; overflow: hidden; background: var(--white); }
  .slide {
    position: relative; width: 1200px; height: 900px; overflow: hidden;
    font-family: "Roboto Condensed", "Arial Narrow", sans-serif;
    background:
      radial-gradient(ellipse 260px 320px at 0 600px, rgba(200,120,210,0.28), rgba(255,255,255,0) 70%),
      var(--white);
  }
  .slide-title {
    position: absolute; left: 42px; top: 14px;
    font-size: 52px; font-weight: 400; color: var(--magenta); letter-spacing: 0.3px;
  }
  .logo-slot {
    position: absolute; left: 1035px; top: 11px; width: 151px; height: 70px;
    border: 2px solid #e4e4e4; border-radius: 9px;
    display: flex; align-items: center; justify-content: center;
    font-size: 28px; color: var(--placeholder); letter-spacing: 1px;
    box-shadow: 0 1px 4px rgba(0,0,0,0.08);
  }
  .title-rule { position: absolute; left: 0; top: 90px; width: 1200px; height: 2px; background: var(--rule); }
  .backdrop {
    position: absolute; left: 880px; top: 93px; width: 320px; height: 745px;
    background:
      linear-gradient(90deg, rgba(255,255,255,1) 0%, rgba(255,255,255,0) 45%),
      linear-gradient(160deg, #d98ae0 0%, #e8b3ea 40%, #f0c8ef 65%, #dc93e0 100%);
  }
  .feature-list { position: absolute; left: 54px; top: 112px; list-style: none; }
  .feature {
    position: absolute; left: 0; display: flex; align-items: center; width: 700px; height: 117px;
  }
  .feature-icon {
    width: 117px; height: 117px; background: var(--tile);
    border: 3px solid var(--tile-edge); box-shadow: 0 1px 5px rgba(0,0,0,0.25);
    display: flex; align-items: center; justify-content: center; flex: none;
  }
  .feature-icon svg { width: 100px; height: 100px; }
  .feature-label { margin-left: 30px; font-size: 38px; color: var(--ink); letter-spacing: 0.4px; }
  .footer { position: absolute; left: 0; top: 838px; width: 1200px; height: 62px; }
  .footer svg { position: absolute; inset: 0; }
  .page-number, .copyright {
    position: absolute; top: 0; height: 62px; display: flex; align-items: center;
    color: var(--white); font-size: 25px; letter-spacing: 0.5px;
  }
  .page-number { left: 13px; }
  .copyright { right: 14px; }
</style>
</head>
<body>
<main class="slide">
  <h1 class="slide-title">Key features</h1>
  <div class="logo-slot">LOGO HERE</div>
  <div class="title-rule"></div>
  <div class="backdrop" role="img" aria-label="Decorative pattern of translucent purple triangles"></div>

  <ul class="feature-list">
    <li class="feature" style="top:0">
      <span class="feature-icon">
        <svg viewBox="0 0 100 100" fill="#fff">
          <circle cx="28" cy="28" r="9"/><circle cx="50" cy="24" r="10"/><circle cx="72" cy="22" r="11"/>
          <path d="M14 66v-20q0-8 8-8h12q8 0 8 8v20z"/>
          <path d="M36 72v-24q0-8 8-8h13q8 0 8 8v24z" stroke="var(--tile)" stroke-width="2"/>
          <path d="M58 80v-30q0-8 8-8h14q8 0 8 8v30z" stroke="var(--tile)" stroke-width="2"/>
        </svg>
      </span>
      <span class="feature-label">Separation of duties</span>
    </li>
    <li class="feature" style="top:135px">
      <span class="feature-icon">
        <svg viewBox="0 0 100 100" fill="#fff">
          <path d="M30 46v-12a20 20 0 0 1 40 0v12" fill="none" stroke="#fff" stroke-width="8"/>
          <rect x="20" y="46" width="60" height="42"/>
        </svg>
      </span>
      <span class="feature-label">Access Control</span>
    </li>
    <li class="feature" style="top:273px">
      <span class="feature-icon">
        <svg viewBox="0 0 100 100" fill="#fff">
          <rect x="18" y="62" width="10" height="28"/><rect x="36" y="34" width="10" height="56"/>
          <rect x="54" y="46" width="10" height="44"/><rect x="72" y="24" width="10" height="66"/>
        </svg>
      </span>
      <span class="feature-label">Visibility</span>
    </li>
    <li class="feature" style="top:410px">
      <span class="feature-icon">
        <svg viewBox="0 0 100 100" fill="#fff">
          <circle cx="36" cy="64" r="15"/>
          <g stroke="#fff" stroke-width="7">
            <path d="M36 42v44M14 64h44M20 48l32 32M52 48l-32 32"/>
          </g>
          <circle cx="36" cy="64" r="6" fill="var(--tile)"/>
          <circle cx="68" cy="32" r="11"/>
          <g stroke="#fff" stroke-width="6">
            <path d="M68 16v32M52 32h32M57 21l22 22M79 21l-22 22"/>
          </g>
          <circle cx="68" cy="32" r="4.5" fill="var(--tile)"/>
        </svg>
      </span>
      <span class="feature-label">Governance processes</span>
    </li>
    <li class="feature" style="top:549px">
      <span class="feature-icon">
        <svg viewBox="0 0 100 100" fill="none" stroke="#fff" stroke-width="3">
          <path d="M50 24v56M32 80h36M18 34h64"/>
          <circle cx="50" cy="26" r="4" fill="#fff"/>
          <path d="M18 34l-10 22M18 34l10 22M82 34l-10 22M82 34l10 22"/>
          <path d="M6 56q12 12 24 0z M70 56q12 12 24 0z" fill="#fff"/>
        </svg>
      </span>
      <span class="feature-label">Compare Orgs</span>
    </li>
  </ul>

  <footer class="footer">
    <svg viewBox="0 0 1200 62" width="1200" height="62">
      <polygon points="0,3 905,3 940,62 0,62" fill="var(--footer-dark)"/>
      <polygon points="920,3 1200,3 1200,62 955,62" fill="var(--footer-light)"/>
    </svg>
    <span class="page-number">Page : 01</span>
    <span class="copyright">Copyright text here</span>
  </footer>
</main>
</body>
</html>
```